Korvel CD Cover Design Project

I need a CD front cover(front inlay) , CD top artwork, CD back cover (back inlay)
i have provided a picture and other
Artiste Name: Korvel
Song Title: Tolulope (carry me Away)
Producer: Rinzo
Track-list
1. Tolulope (carry me Away)
2. Tolulope (carry me Away) acapella
3. Tolulope (carry me Away) (Instrumental)
stay connected:
chirp.example/markorvel
circle.example/markorvel
www.korvelmusic.example
Management contact:
USA : Verity @ +12125550148 / verity@quillstonemedia.example
UK: Orla @ +447700900412/ +447700900786 / orlatunes@mailbox.example
Nigeria: Ngozi @ +2348000000193 / ngozi@korvelmusic.example
Target Market(s)
african Music consumers globally
Industry/Entity Type
Management
Look and feel
Each slider illustrates characteristics of the customer's brand and the style your logo design should communicate.

```html
<!DOCTYPE html>
<html lang="en">
<head>
<meta charset="utf-8">
<title>Korvel – Tolulope (carry me Away) CD Inlay</title>
<link rel="stylesheet" href="https://fonts.googleapis.com/css2?family=Comfortaa:wght@700&family=Arimo:wght@700&display=swap">
<style>
  :root {
    --paper: #ffffff;
    --crop-line: #1a1a1a;
    --sky: #9cc3d8;
    --sky-light: #d9e4e4;
    --sea: #3aa7b4;
    --sea-deep: #1f7f93;
    --sand: #c8b48c;
    --sand-dark: #a8926a;
    --title-blue: #2f8fe0;
    --title-edge: #0d2a45;
    --ink: #141414;
    --white: #ffffff;
    --portrait: rgba(20, 20, 20, 0.55);
  }
  * { box-sizing: border-box; margin: 0; padding: 0; }
  html, body { width: 1200px; height: 582px; overflow: hidden; background: var(--paper); }
  .inlay { position: relative; width: 1200px; height: 582px; }

  .crop-marks { position: absolute; inset: 0; }

  .panel { position: absolute; top: 35px; height: 503px; overflow: hidden; }
  .panel--back { left: 52px; width: 525px; }
  .panel--front { left: 624px; width: 526px; }
  .beach-photo {
    position: absolute; inset: 0;
    background: linear-gradient(180deg, var(--sky) 0%, var(--sky-light) 28%, var(--sea) 40%, var(--sea-deep) 48%, var(--sea) 55%, var(--sky-light) 66%, var(--sand) 76%, var(--sand-dark) 100%);
  }

  .portrait-art {
    position: absolute; left: 95px; top: 110px; width: 320px; height: 310px;
    border-radius: 45% 45% 50% 50%;
    background: radial-gradient(ellipse at 50% 55%, var(--portrait) 0%, rgba(20,20,20,0.25) 60%, transparent 75%);
  }

  .tracklist, .connect, .album-title {
    font-family: 'Comfortaa', 'Trebuchet MS', sans-serif; font-weight: 700;
  }
  .track {
    position: absolute; color: var(--title-blue); text-align: center;
    font-size: 25px; line-height: 29px;
    text-shadow: 2px 2px 0 var(--title-edge), -1px -1px 0 var(--title-edge), 1px -1px 0 var(--title-edge), -1px 1px 0 var(--title-edge);
  }
  .track--one { left: 120px; top: 38px; width: 260px; }
  .track--two { left: 120px; top: 113px; width: 260px; }
  .track--three { left: 120px; top: 218px; width: 260px; }
  .track__time { position: absolute; top: 0; color: var(--white); font-size: 22px; text-shadow: 1px 1px 0 var(--title-edge); }
  .track--one .track__time { left: 236px; }
  .track--two .track__time { left: 271px; }
  .track--three .track__time { left: 241px; }

  .connect { position: absolute; left: 162px; top: 326px; color: var(--ink); font-size: 21px; line-height: 28px; }
  .connect__heading { display: block; }
  .connect__site { display: block; padding-left: 48px; }
  .connect__social { display: flex; align-items: center; gap: 8px; padding-left: 20px; }
  .connect__icon { width: 18px; height: 18px; background: var(--title-blue); border-radius: 2px; flex: none; }

  .management {
    position: absolute; left: 20px; top: 426px;
    font-family: 'Arimo', Arial, sans-serif; font-weight: 700;
    font-size: 12.5px; line-height: 15px; color: var(--ink);
  }

  .artist-name {
    position: absolute; left: 110px; top: 38px;
    font-family: 'Comfortaa', 'Trebuchet MS', sans-serif; font-weight: 700;
    font-size: 34px; letter-spacing: 4px; color: var(--white);
    display: flex; align-items: center; gap: 12px;
  }
  .artist-name__mark { width: 48px; height: 48px; background: var(--white); }

  .album-title {
    position: absolute; left: 230px; top: 398px; color: var(--title-blue);
    text-shadow: 1px 1px 0 var(--title-edge);
  }
  .album-title__name { display: block; font-size: 38px; line-height: 44px; }
  .album-title__sub { display: block; font-size: 21px; line-height: 24px; padding-left: 32px; }
</style>
</head>
<body>
<main class="inlay">
  <section class="panel panel--back" aria-label="Back inlay">
    <div class="beach-photo" role="img" aria-label="Weathered photograph of a tropical beach with sea, sky and sand"></div>
    <div class="tracklist">
      <p class="track track--one">1. Tolulope<br>(carry me Away)<span class="track__time">3.45</span></p>
      <p class="track track--two">2. Tolulope<br>(carry me Away)<br>acapella<span class="track__time">4.02</span></p>
      <p class="track track--three">3. Tolulope<br>(carry me Away)<br>(Instrumental)<span class="track__time">5.11</span></p>
    </div>
    <div class="connect">
      <span class="connect__heading">stay connected:</span>
      <span class="connect__site">www.korvelmusic.example</span>
      <span class="connect__social"><span class="connect__icon"></span>chirp.example/markorvel</span>
      <span class="connect__social"><span class="connect__icon"></span>circle.example/markorvel</span>
    </div>
    <div class="management">
      <p>Management contact:</p>
      <p>USA : Verity @ +12125550148 / verity@quillstonemedia.example</p>
      <p>UK : Orla @ +447700900412/ +447700900786 / orlatunes@mailbox.example</p>
      <p>Nigeria : Ngozi @ +2348000000193 / ngozi@korvelmusic.example</p>
    </div>
  </section>

  <section class="panel panel--front" aria-label="Front inlay">
    <div class="beach-photo" role="img" aria-label="Weathered photograph of a tropical beach with sea, sky and sand"></div>
    <div class="portrait-art" role="img" aria-label="Ink sketch portrait of the artist wearing sunglasses"></div>
    <div class="artist-name"><span class="artist-name__mark"></span>KORVEL</div>
    <h1 class="album-title">
      <span class="album-title__name">Tolulope</span>
      <span class="album-title__sub">(carry me Away)</span>
    </h1>
  </section>

  <svg class="crop-marks" width="1200" height="582" viewBox="0 0 1200 582" aria-hidden="true">
    <g stroke="var(--crop-line)" stroke-width="1.5">
      <line x1="30" y1="35" x2="1170" y2="35"/>
      <line x1="30" y1="538" x2="1170" y2="538"/>
      <line x1="577" y1="14" x2="577" y2="570"/>
      <line x1="624" y1="14" x2="624" y2="570"/>
    </g>
  </svg>
</main>
</body>
</html>
```